Business Card Design for Training Business

Clear Path Coaching is a new business that delivers training and other services with a focus on topics related to mental health and wellbeing, for example, Wellmind Response Course, Resilience etc. We have a strong focus on evidence-based psychology and neuroscience. I have a logo which I will upload with the brief, so please consider colours that work well with the logo.
Target Market(s)
Adults, workplaces (particularly government and not-for-profits)
Industry/Entity Type
Business
Contact Information for Business Card
Head Strong TrainingSamantha SellwoodDirector0438 770 850sam@headstrongtraining.com.auwww.headstrongtraining.com.au

```html
<!DOCTYPE html>
<html lang="en">
<head>
<meta charset="utf-8">
<title>Clear Path Coaching – Business Card</title>
<link rel="stylesheet" href="https://fonts.googleapis.com/css2?family=Open+Sans:wght@400&display=swap">
<style>
  :root {
    --backdrop: #f1e4cc;
    --card: #ffffff;
    --teal: #118c8f;
    --teal-soft: #8fd0cf;
    --ink: #111111;
    --taupe: #6f625c;
  }
  html, body {
    margin: 0;
    width: 1200px;
    height: 894px;
    overflow: hidden;
    background: var(--backdrop);
    font-family: "Open Sans", Arial, sans-serif;
  }
  .card {
    position: absolute;
    left: 150px;
    top: 190px;
    width: 900px;
    height: 514px;
    background: var(--card);
    box-shadow: 0 6px 24px rgba(90, 70, 40, 0.18);
    overflow: hidden;
  }
  .card__swoosh {
    position: absolute;
    inset: 0;
  }
  .brand {
    position: absolute;
    right: 96px;
    top: 118px;
    display: flex;
    align-items: center;
    gap: 18px;
  }
  .brand__dot {
    width: 64px;
    height: 64px;
    border-radius: 50%;
    background: var(--teal-soft);
  }
  .brand__name {
    font-size: 30px;
    letter-spacing: 4px;
    color: var(--taupe);
    text-transform: uppercase;
    line-height: 1.2;
  }
  .person {
    position: absolute;
    right: 96px;
    top: 238px;
    text-align: right;
  }
  .person__name {
    margin: 0;
    font-size: 40px;
    font-weight: 400;
    color: var(--teal);
    line-height: 1.1;
  }
  .person__role {
    margin: 2px 0 0;
    font-size: 22px;
    color: var(--ink);
  }
  .contacts {
    position: absolute;
    right: 60px;
    top: 356px;
    margin: 0;
    padding: 0;
    list-style: none;
  }
  .contacts__item {
    display: flex;
    justify-content: flex-end;
    align-items: center;
    gap: 22px;
    height: 32px;
    font-size: 21px;
    color: var(--ink);
  }
  .contacts__icon {
    width: 22px;
    height: 22px;
    flex: none;
  }
</style>
</head>
<body>
  <main class="card">
    <svg class="card__swoosh" viewBox="0 0 900 514" width="900" height="514" aria-hidden="true">
      <path d="M0,0 H720 C450,20 120,150 0,410 Z" fill="var(--ink)"/>
      <path d="M0,0 H650 C400,8 90,110 0,368 Z" fill="var(--teal)"/>
    </svg>

    <div class="brand">
      <span class="brand__dot"></span>
      <span class="brand__name">Clear Path<br>Coaching</span>
    </div>

    <div class="person">
      <h1 class="person__name">Rebecca Tanfield</h1>
      <p class="person__role">Director</p>
    </div>

    <ul class="contacts">
      <li class="contacts__item">
        <span>0491 362 517</span>
        <svg class="contacts__icon" viewBox="0 0 22 22" aria-label="Phone">
          <rect width="22" height="22" fill="var(--ink)"/>
          <path d="M7 5 L9.5 5 L10.5 8 L9 9.5 C10 11.5 11 12.5 12.8 13.3 L14.3 11.8 L17 13 L17 15.5 C11 16.5 5.5 11 7 5 Z" fill="#fff"/>
        </svg>
      </li>
      <li class="contacts__item">
        <span>bec@clearpathcoaching.example.au</span>
        <svg class="contacts__icon" viewBox="0 0 22 22" aria-label="Email">
          <rect width="22" height="22" fill="var(--ink)"/>
          <rect x="4" y="6.5" width="14" height="9.5" fill="none" stroke="#fff" stroke-width="1.4"/>
          <path d="M4 6.5 L11 12 L18 6.5" fill="none" stroke="#fff" stroke-width="1.4"/>
        </svg>
      </li>
      <li class="contacts__item">
        <span>www.clearpathcoaching.example.au</span>
        <svg class="contacts__icon" viewBox="0 0 22 22" aria-label="Website">
          <rect width="22" height="22" fill="var(--ink)"/>
          <circle cx="11" cy="11" r="6.5" fill="none" stroke="#fff" stroke-width="1.4"/>
          <ellipse cx="11" cy="11" rx="2.8" ry="6.5" fill="none" stroke="#fff" stroke-width="1.2"/>
          <path d="M4.5 11 H17.5" stroke="#fff" stroke-width="1.2"/>
        </svg>
      </li>
    </ul>
  </main>
</body>
</html>
```